Web Site Design for a Finance (lending) Company

We are opening a new subsidiary that focuses on lending money in the real estate industry. We need a web site designed to represent the business.

The business is lending money to real estate investors. A typical client/borrower will be looking to borrow money to buy a house, renovate it and then sell it at a profit, all within 12 months or less.

Company name is RTV Finance. Our logo is attached.

Attached is a general outline for the web site. We're working on writing more text for each page but this should give you enough to get started with some ideas.

Competitor web site that I like a lot (as an example): https://dorvaleqcapital.example/. Many of the general items on this site match what we will need (description of loan programs, FAQ)

Target Market(s)

Real estate investors (generally individuals or small companies with just a few people) who are buying homes, renovating them and then selling them at a profit.

Industry/Entity Type

Finance

Coding

Coded - Design and coding required

Number of Pages Required

5+ page

Colors

Designer to choose colors to be used in the design.

Requirements
Must have
• Minimalist design. Clean lines without too much clutter. Some stock photography is ok but the photos should not be distracting. They should almost fade in to the background so that user can focus on the key information about what our company does instead. We are a finance company, not a design company, so the information about our products will be more interesting to site visitors than the art.
• Some minimalist examples from Snapboard:
• https://www.snapboardia.example/explore/minimalist-web-design/
Nice to have
• If you search in zoovle for "hard money lenders" you will find many examples of web sites from our competition. I have provided a link above to competitor web site that I like a lot.
• I have attached our logo in EPS format. Logo is green. Web site doesn't have to be green but it should be of a color that will work well with the logo.

```html
<!DOCTYPE html>
<html lang="en">
<head>
<meta charset="utf-8">
<title>RTV Finance</title>
<link href="https://fonts.googleapis.com/css2?family=Montserrat:wght@700&family=Roboto:wght@300;400;500;700&display=swap" rel="stylesheet">
<style>
:root{
  --green:#0c4d34;
  --green-deep:#083d29;
  --teal-overlay:rgba(14,92,72,.86);
  --ink:#333;
  --muted:#8a8a8a;
  --paper:#f3f2ef;
  --white:#fff;
}
*{margin:0;padding:0;box-sizing:border-box}
html,body{width:1200px;height:2899px;overflow:hidden;background:var(--white)}
body{font-family:'Roboto',Arial,sans-serif;color:var(--ink);position:relative}
section,header,footer{position:absolute;left:0;width:1200px}
.abs{position:absolute}

/* header */
.site-header{top:0;height:112px;background:var(--white)}
.brand{left:99px;top:30px;display:flex;align-items:center;gap:12px;color:var(--green);font-weight:700;font-size:30px}
.brand-square{width:22px;height:22px;background:var(--green)}
.main-nav{right:0;top:46px;display:flex;align-items:center;font-size:14px;font-weight:500;color:var(--green-deep)}
.main-nav a{position:absolute;white-space:nowrap;color:inherit;text-decoration:none}
.login{background:var(--green);color:var(--white)!important;width:95px;height:32px;line-height:32px;text-align:center;top:-8px}

/* hero */
.hero{top:112px;height:642px}
.hero-photo{position:absolute;inset:0;background:linear-gradient(100deg,#5b3a26 0%,#8b5a33 22%,#5d6a4a 40%,#8896a6 62%,#b9c1c9 80%,#707880 100%)}
.hero-shade{position:absolute;inset:0;background:linear-gradient(180deg,rgba(0,0,0,.15),rgba(0,0,0,.25))}
.hero-curve{position:absolute;left:0;bottom:-1px}
.hero h1{position:absolute;top:158px;width:100%;text-align:center;font-family:'Montserrat',Arial,sans-serif;font-size:48px;line-height:58px;color:var(--white)}
.hero .lede{position:absolute;top:284px;width:100%;text-align:center;font-size:19px;color:var(--white)}
.btn{display:block;background:var(--green);color:var(--white);text-align:center;font-weight:500;text-decoration:none}
.hero .btn{position:absolute;left:519px;top:340px;width:162px;height:44px;line-height:44px;font-size:18px}
.chev{position:absolute;top:270px}

/* welcome */
.welcome{top:754px;height:479px}
.section-title{position:absolute;width:100%;text-align:center;font-weight:400;color:var(--green);font-size:37px}
.welcome .section-title{top:42px}
.points{position:absolute;left:99px;top:118px;width:960px;list-style:none;font-size:19px;line-height:28px;color:#444}
.points li{position:relative;padding-left:36px;margin-bottom:38px}
.points svg{position:absolute;left:0;top:3px}
.welcome .btn{position:absolute;left:471px;top:324px;width:256px;height:51px;line-height:51px;font-size:19px}

/* loans */
.loans{top:1233px;height:510px}
.loans-photo{position:absolute;inset:0;background:linear-gradient(180deg,#4f7f77 0%,#3f7060 55%,#2e5c3a 100%)}
.loans-overlay{position:absolute;inset:0;background:var(--teal-overlay)}
.loans .section-title{top:70px;color:var(--white);font-weight:300}
.loan{position:absolute;top:160px;width:420px;color:var(--white)}
.loan-mark{width:64px;height:40px;border:3px solid var(--white);margin:0 0 16px 110px;border-bottom:none}
.loan h3{font-size:27px;font-weight:700;text-transform:uppercase;margin-bottom:22px;letter-spacing:-.2px}
.loan ul{list-style:none;font-size:12.5px;line-height:16px}
.loan li{position:relative;padding-left:18px;margin-bottom:8px}
.loan li svg{position:absolute;left:0;top:3px}

/* why */
.why{top:1743px;height:406px;background:var(--paper)}
.why .section-title{top:64px;color:var(--green-deep)}
.feature{position:absolute;top:179px;width:200px;text-align:center}
.feature-icon{width:108px;height:108px;border-radius:50%;background:var(--green);border:4px solid var(--white);box-shadow:0 0 0 2px var(--green);margin:0 auto 22px;display:flex;align-items:center;justify-content:center}
.feature span{font-size:14px;font-weight:500;color:var(--muted);text-transform:uppercase}

/* membership */
.membership{top:2149px;height:405px}
.membership .section-title{top:62px}
.membership p{position:absolute;left:200px;top:130px;width:800px;text-align:center;font-size:12.5px;line-height:25px;color:var(--muted)}
.member{position:absolute;top:208px;width:155px;height:93px;border:1px solid #ddd;background:var(--white);display:flex;align-items:center;justify-content:center}
.member i{display:block;width:90px;height:34px;background:#cfcfcf}
.live-chat{position:absolute;left:1028px;top:359px;width:72px;height:42px;background:var(--green);color:var(--white);font-size:11px;font-weight:700;text-align:center;line-height:42px;border-radius:4px}

/* footer */
.site-footer{top:2554px;height:345px;background:var(--green);color:var(--white)}
.site-footer h4{position:absolute;top:50px;font-size:18px;font-weight:500;text-transform:uppercase}
.f-links{position:absolute;top:100px;list-style:none;font-size:14px;line-height:32px}
.col-rule{position:absolute;top:50px;width:1px;height:200px;background:rgba(255,255,255,.15)}
.contact{position:absolute;left:487px;top:98px;font-size:14px;line-height:26px}
.contact .row{display:flex;align-items:center;gap:10px}
.news{position:absolute;left:775px;top:92px;font-size:14px}
.signup{display:flex;margin-top:18px}
.signup .field{width:221px;height:38px;background:var(--white);color:#aaa;font-size:13px;line-height:38px;padding-left:14px}
.signup .go{width:106px;height:38px;background:#062e1f;font-size:14px;font-weight:500;line-height:38px;text-align:center}
.socials{display:flex;gap:10px;margin-top:14px}
.socials i{width:38px;height:38px;border-radius:50%;background:var(--white)}
.foot-rule{position:absolute;left:99px;top:272px;width:1002px;height:1px;background:rgba(255,255,255,.45)}
.copy{position:absolute;left:99px;top:296px;font-size:14px}
</style>
</head>
<body>

<header class="site-header">
  <div class="abs brand"><span class="brand-square"></span>RTV Finance</div>
  <nav class="abs main-nav" style="left:0;width:1200px">
    <a href="#" style="left:450px">HOME</a>
    <a href="#" style="left:540px">ABOUT US</a>
    <a href="#" style="left:656px">LOANS</a>
    <a href="#" style="left:751px">RESOURCES</a>
    <a href="#" style="left:882px">CONTACT US</a>
    <a href="#" class="login" style="left:1006px">LOGIN</a>
  </nav>
</header>

<section class="hero">
  <div class="hero-photo" role="img" aria-label="Photo of a suburban house with a garage and an autumn tree on the lawn"></div>
  <div class="hero-shade"></div>
  <svg class="chev" style="left:30px" width="16" height="30" viewBox="0 0 16 30"><path d="M14 2 2 15l12 13" fill="none" stroke="#fff" stroke-width="2"/></svg>
  <svg class="chev" style="left:1144px" width="16" height="30" viewBox="0 0 16 30"><path d="M2 2l12 13L2 28" fill="none" stroke="#fff" stroke-width="2"/></svg>
  <h1>Local real estate experts lending to<br>local real estate investors</h1>
  <div class="lede">We are opening a new subsidiary that focuses on lending money in the real estate industry</div>
  <a class="btn" href="#">LEARN MORE</a>
  <svg class="hero-curve" width="1200" height="70" viewBox="0 0 1200 70" preserveAspectRatio="none"><path d="M0 70V58Q600-40 1200 62V70Z" fill="#fff"/></svg>
</section>

<section class="welcome">
  <h2 class="section-title">Welcome to RTV Finance</h2>
  <ul class="points">
    <li><svg width="26" height="26" viewBox="0 0 26 26"><circle cx="13" cy="13" r="13" fill="#0c4d34"/><path d="M7 13.5l4 4 8-8" fill="none" stroke="#fff" stroke-width="3"/></svg>RTV Finance is a local business with local knowledge and strong industry relationships. A partner with a wide network &nbsp; who offers value added services.</li>
    <li><svg width="26" height="26" viewBox="0 0 26 26"><circle cx="13" cy="13" r="13" fill="#0c4d34"/><path d="M7 13.5l4 4 8-8" fill="none" stroke="#fff" stroke-width="3"/></svg>RTV has an established pool of experienced investors available for your real estate investment needs</li>
  </ul>
  <a class="btn" href="#">APPLY NOW</a>
</section>

<section class="loans">
  <div class="loans-photo" role="img" aria-label="Soft background photo of city towers behind green trees"></div>
  <div class="loans-overlay"></div>
  <h2 class="section-title">Loans offered RTV Finance</h2>
  <div class="loan" style="left:110px">
    <div class="loan-mark"></div>
    <h3>Fix and Flip Loans</h3>
    <ul>
      <li><svg width="11" height="10" viewBox="0 0 11 10"><path d="M1 5l3 3 6-7" fill="none" stroke="#fff" stroke-width="2"/></svg>Description of the loan type, borrower requirements</li>
      <li><svg width="11" height="10" viewBox="0 0 11 10"><path d="M1 5l3 3 6-7" fill="none" stroke="#fff" stroke-width="2"/></svg>Loan terms table (fee, rate, loan to cost etc.) [Let me know if you want this and what info you want to include on the website]</li>
      <li><svg width="11" height="10" viewBox="0 0 11 10"><path d="M1 5l3 3 6-7" fill="none" stroke="#fff" stroke-width="2"/></svg>Why choose RTV</li>
      <li><svg width="11" height="10" viewBox="0 0 11 10"><path d="M1 5l3 3 6-7" fill="none" stroke="#fff" stroke-width="2"/></svg>Online application or Contact web form [Do you want application or just contact us webform? If application, we'll need to know what fields should be included]</li>
    </ul>
  </div>
  <div class="loan" style="left:657px;width:450px">
    <div class="loan-mark" style="margin-left:160px"></div>
    <h3>Commercial Hard Money Loans</h3>
    <ul>
      <li><svg width="11" height="10" viewBox="0 0 11 10"><path d="M1 5l3 3 6-7" fill="none" stroke="#fff" stroke-width="2"/></svg>Description of the loan type, borrower requirements</li>
      <li><svg width="11" height="10" viewBox="0 0 11 10"><path d="M1 5l3 3 6-7" fill="none" stroke="#fff" stroke-width="2"/></svg>Loan terms table (fee, rate, loan to cost etc.)</li>
      <li><svg width="11" height="10" viewBox="0 0 11 10"><path d="M1 5l3 3 6-7" fill="none" stroke="#fff" stroke-width="2"/></svg>Why choose RTV</li>
      <li><svg width="11" height="10" viewBox="0 0 11 10"><path d="M1 5l3 3 6-7" fill="none" stroke="#fff" stroke-width="2"/></svg>Online application or Contact web form [Do you want application or just contact us webform? If application, we'll need to know what fields should be included]</li>
    </ul>
  </div>
</section>

<section class="why">
  <h2 class="section-title">Why Borrow from RTV</h2>
  <div class="feature" style="left:53px"><div class="feature-icon"><svg width="46" height="46" viewBox="0 0 46 46"><circle cx="20" cy="14" r="8" fill="#fff"/><path d="M5 40q2-14 15-14 8 0 12 5" fill="#fff"/><path d="M26 34l5 5 10-12" fill="none" stroke="#fff" stroke-width="4"/></svg></div><span>Experts</span></div>
  <div class="feature" style="left:221px"><div class="feature-icon"><svg width="44" height="44" viewBox="0 0 44 44"><rect x="4" y="20" width="8" height="20" fill="#fff"/><path d="M15 20l8-14q4 0 3 6l-1 6h12q4 1 3 5l-3 13q-1 4-5 4H15Z" fill="#fff"/></svg></div><span>Fast Approval</span></div>
  <div class="feature" style="left:389px"><div class="feature-icon"><svg width="44" height="44" viewBox="0 0 44 44"><rect x="6" y="28" width="8" height="12" fill="#fff"/><rect x="18" y="20" width="8" height="20" fill="#fff"/><rect x="30" y="12" width="8" height="28" fill="#fff"/><path d="M6 20 34 4" stroke="#fff" stroke-width="3"/></svg></div><span>Professional</span></div>
  <div class="feature" style="left:557px"><div class="feature-icon"><svg width="50" height="40" viewBox="0 0 50 40"><path d="M2 14l10-6 8 4 6-3 10 3 12 0M2 14l4 10 14 10 6-4 6 2 10-10 6-8" fill="none" stroke="#fff" stroke-width="3.5" stroke-linejoin="round"/></svg></div><span>A Partner</span></div>
  <div class="feature" style="left:721px"><div class="feature-icon"><svg width="44" height="44" viewBox="0 0 44 44"><rect x="6" y="6" width="26" height="32" fill="none" stroke="#fff" stroke-width="3"/><path d="M16 30 38 8" stroke="#fff" stroke-width="4"/></svg></div><span>Selective</span></div>
  <div class="feature" style="left:885px;width:232px"><div class="feature-icon"><svg width="46" height="46" viewBox="0 0 46 46"><circle cx="26" cy="15" r="11" fill="#fff"/><text x="26" y="21" font-family="Roboto,Arial,sans-serif" font-size="16" font-weight="700" fill="#0c4d34" text-anchor="middle">$</text><path d="M2 36q8-8 16-6l10 2q4 2 0 4H18m-16 6h28l14-10q-2-3-6-2l-8 4" fill="none" stroke="#fff" stroke-width="3"/></svg></div><span>Competitive Rates and Fees</span></div>
</section>

<section class="membership">
  <h2 class="section-title">Our Membership</h2>
  <p>Neque porro quisquam est, qui dolorem ipsum quia dolor sit amet, consectetur, adipisci velit, sed quia non numquam eius modi tempora incidunt ut labore et dolore magnam aliquam quaerat voluptatem.</p>
  <svg class="abs" style="left:56px;top:242px" width="16" height="26" viewBox="0 0 16 26"><path d="M13 2 3 13l10 11" fill="none" stroke="#bbb" stroke-width="3"/></svg>
  <div class="member" style="left:99px"><i></i></div>
  <div class="member" style="left:268px"><i></i></div>
  <div class="member" style="left:438px"><i></i></div>
  <div class="member" style="left:607px"><i></i></div>
  <div class="member" style="left:777px"><i></i></div>
  <div class="member" style="left:946px"><i></i></div>
  <svg class="abs" style="left:1130px;top:242px" width="16" height="26" viewBox="0 0 16 26"><path d="M3 2l10 11L3 24" fill="none" stroke="#bbb" stroke-width="3"/></svg>
  <div class="live-chat">LIVE CHAT!</div>
</section>

<footer class="site-footer">
  <h4 style="left:99px">Quick Links</h4>
  <ul class="f-links" style="left:99px"><li>Home</li><li>About us</li><li>Loans</li><li>Resources</li></ul>
  <ul class="f-links" style="left:280px"><li>Terms of Service</li><li>Privacy Policy</li><li>Contact Us</li></ul>
  <div class="col-rule" style="left:425px"></div>
  <h4 style="left:487px">Contact Info</h4>
  <div class="contact">
    <div>RTV Finance , Street Name, City<br>Address, Country Name, Code.</div>
    <div class="row" style="margin-top:6px"><svg width="14" height="14" viewBox="0 0 14 14"><path d="M3 1l3 3-2 2q2 3 4 4l2-2 3 3-2 2Q5 13 1 3Z" fill="#fff"/></svg>+00 123 45 67 890</div>
    <div class="row" style="margin-top:6px"><svg width="14" height="12" viewBox="0 0 14 12"><rect x="1" y="1" width="12" height="10" fill="#fff"/><path d="M1 1l6 5 6-5" fill="none" stroke="#0c4d34" stroke-width="1.5"/></svg>info@rtvfinance.example</div>
  </div>
  <div class="col-rule" style="left:727px"></div>
  <h4 style="left:775px">Sign up for Newsletters</h4>
  <div class="news">
    Please sign up here for latest news
    <div class="signup"><div class="field">EMAIL ADDRESS</div><div class="go">SUBSCRIBE</div></div>
    <div class="socials"><i></i><i></i><i></i><i></i></div>
  </div>
  <div class="foot-rule"></div>
  <div class="copy">© 2017 RTV FINANCE. &nbsp;All right reserved . Term of Use</div>
</footer>

</body>
</html>
```